Personal Injury Lawyer Billboard

I would like a design created featuring the image of the lawyer centered in the middle of the design.
To the left of the lawyer's image it should read "INJURED?"
To the right of the lawyer's image, it should read "CALL DEAN!"
Under Call Dean, include the phone number 318-555-0187.
At the bottom of the design include the lawyers information "Dean Marlowe Accident & Injury Lawyers"
PLEASE REMOVED THE BACKGROUND IMAGERY OF THE PHOTO SUBMITTED. Also, the colors for this design should match the colors shown in the logo (navy, white and relective soft gold). Please use those color combinations in ways that best stand out.

```html
<!DOCTYPE html>
<html lang="en">
<head>
<meta charset="utf-8">
<title>Dean Marlowe Accident &amp; Injury Lawyers – Billboard</title>
<link rel="stylesheet" href="https://fonts.googleapis.com/css2?family=Cinzel:wght@500&family=Playfair+Display:wght@700&display=swap">
<style>
  :root {
    --navy: #0b1a45;
    --gold: #cfa94a;
    --gold-panel: #c39d3d;
    --white: #ffffff;
    --backdrop: #e9ebef;
  }
  * { margin: 0; padding: 0; box-sizing: border-box; }
  html, body {
    width: 1200px;
    height: 879px;
    overflow: hidden;
    background: var(--backdrop);
  }
  .billboard {
    position: absolute;
    left: 0;
    top: 206px;
    width: 1200px;
    height: 466px;
    background: var(--navy);
    overflow: hidden;
  }
  .headline {
    position: absolute;
    left: 38px;
    top: 140px;
    font-family: "Cinzel", serif;
    font-weight: 500;
    font-size: 74px;
    letter-spacing: 3px;
    color: var(--gold);
    line-height: 1;
  }
  .portrait {
    position: absolute;
    left: 456px;
    top: 0;
    width: 352px;
    height: 462px;
    border-radius: 22px;
    background: linear-gradient(180deg, var(--gold-panel) 0%, var(--gold-panel) 30%, #8a7a4f 62%, #1a2550 100%);
  }
  .firm-name {
    position: absolute;
    left: 20px;
    top: 316px;
    width: 412px;
    font-family: "Playfair Display", serif;
    font-weight: 700;
    color: var(--white);
    text-align: center;
    line-height: 1;
  }
  .firm-name .name {
    display: block;
    font-size: 50px;
    letter-spacing: -0.5px;
  }
  .firm-name .practice {
    display: block;
    margin-top: 22px;
    font-size: 24px;
    letter-spacing: 0.2px;
  }
  .contact {
    position: absolute;
    left: 820px;
    top: 130px;
    width: 356px;
    text-align: center;
    font-family: "Cinzel", serif;
    font-weight: 500;
    color: var(--gold);
  }
  .contact .call {
    display: block;
    font-size: 56px;
    line-height: 1;
    letter-spacing: 1px;
  }
  .contact .phone-icon {
    display: block;
    margin: 22px auto 0;
    width: 66px;
    height: 66px;
  }
  .contact .number {
    display: block;
    margin-top: 14px;
    font-size: 38px;
    line-height: 1;
    letter-spacing: 0.5px;
  }
</style>
</head>
<body>
  <main class="billboard">
    <h1 class="headline">INJURED</h1>

    <div class="portrait" role="img" aria-label="Photo of attorney Dean Marlowe in a navy suit and green tie, smiling with a raised fist, on a soft gold panel"></div>

    <p class="firm-name">
      <span class="name">DEAN MARLOWE</span>
      <span class="practice">ACCIDENT &amp; INJURY LAWYERS</span>
    </p>

    <div class="contact">
      <span class="call">CALL DEAN</span>
      <svg class="phone-icon" viewBox="0 0 66 66" aria-hidden="true">
        <circle cx="33" cy="33" r="30" fill="none" stroke="var(--gold)" stroke-width="3"/>
        <path d="M22 19c2-2 4-2 5 0l3 6c1 2 0 3-1 4l-2 2c2 4 5 7 9 9l2-2c1-1 2-2 4-1l6 3c2 1 2 3 0 5l-3 3c-3 2-9 0-15-6s-9-13-6-16z" fill="var(--gold)"/>
        <path d="M36 19a11 11 0 0 1 11 11M36 24a6 6 0 0 1 6 6" fill="none" stroke="var(--gold)" stroke-width="2.5" stroke-linecap="round"/>
      </svg>
      <span class="number">318-555-0187</span>
    </div>
  </main>
</body>
</html>
```